New National Dermatology Group needs a business card!

We need a business card for our new national company that has 3 brands within the business:
Lumora Clinics Australia, Tessaly Clinics Australia and Corvane Clinics Australia.
We help people access dermatology services close to home throughout Australia.
We need a business card that has:
all 3 logos on it,
Our websites (there are three, listed above)
Our email (there are three, listed above)
The location of our first clinic: 41 Willow Rd Parramatta (this can then be changed for each location as required)

```html
<!DOCTYPE html>
<html lang="en">
<head>
<meta charset="utf-8">
<title>Clinics Australia business card</title>
<link rel="stylesheet" href="https://fonts.googleapis.com/css2?family=Source+Sans+3:wght@400;600&display=swap">
<style>
:root{
  --brown:#7a3b1b;
  --green:#22b04b;
  --orange:#f3822b;
  --white:#ffffff;
  --stage:#ecebe9;
  --sans:"Source Sans 3", Arial, sans-serif;
}
*{margin:0;padding:0;box-sizing:border-box}
html,body{width:1200px;height:1181px;overflow:hidden}
body{background:var(--stage);font-family:var(--sans);position:relative}
.card{position:absolute;width:654px;height:403px;overflow:hidden;box-shadow:0 6px 18px rgba(0,0,0,.12)}
.card-front{left:180px;top:156px}
.card-back{left:479px;top:627px;background:var(--white)}
.bands{position:absolute;inset:0}
.brand-name{position:absolute;font-weight:600;font-size:27px;line-height:1;letter-spacing:0;white-space:nowrap}
.card-front .brand-name{left:30px;color:var(--white)}
.card-back .brand-name{left:190px}
.brand-corvane{color:var(--brown)}
.brand-lumora{color:var(--green)}
.brand-tessaly{color:var(--orange)}
.contact{position:absolute;right:36px;color:var(--white);text-align:right;font-size:18px;line-height:1}
.contact-line{display:flex;justify-content:flex-end;align-items:center;gap:7px;height:23px}
.contact-line svg{width:19px;height:19px}
.contact-address{margin-top:8px}
.side-bar{position:absolute;width:10px;height:64px}
.side-bar.left{left:0}
.side-bar.right{right:0}
</style>
</head>
<body>

<section class="card card-front">
  <svg class="bands" viewBox="0 0 654 403" preserveAspectRatio="none">
    <rect width="654" height="403" fill="var(--orange)"/>
    <polygon points="0,0 654,0 654,299 384,299 281,249 0,249" fill="var(--green)"/>
    <polygon points="0,0 654,0 654,166 368,166 265,115 0,115" fill="var(--brown)"/>
  </svg>

  <p class="brand-name" style="top:39px">Corvane Clinics Australia</p>
  <div class="contact" style="top:44px">
    <div class="contact-line">info@corvane.co.uk
      <svg viewBox="0 0 20 20"><rect x="1" y="4" width="18" height="12" fill="none" stroke="#fff" stroke-width="1.6"/><path d="M1 4l9 7 9-7M1 16l7-6M19 16l-7-6" fill="none" stroke="#fff" stroke-width="1.6"/></svg></div>
    <div class="contact-line">www.corvane.co.uk
      <svg viewBox="0 0 20 20"><circle cx="10" cy="10" r="8.5" fill="none" stroke="#fff" stroke-width="1.6"/><ellipse cx="10" cy="10" rx="3.6" ry="8.5" fill="none" stroke="#fff" stroke-width="1.4"/><path d="M1.5 10h17M3 6h14M3 14h14" stroke="#fff" stroke-width="1.4"/></svg></div>
    <div class="contact-address">41 Willow Rd Parramatta</div>
  </div>

  <p class="brand-name" style="top:157px">Lumora Clinics Australia</p>
  <div class="contact" style="top:183px">
    <div class="contact-line">info@lumora.co.uk
      <svg viewBox="0 0 20 20"><rect x="1" y="4" width="18" height="12" fill="none" stroke="#fff" stroke-width="1.6"/><path d="M1 4l9 7 9-7M1 16l7-6M19 16l-7-6" fill="none" stroke="#fff" stroke-width="1.6"/></svg></div>
    <div class="contact-line">www.lumora.co.uk
      <svg viewBox="0 0 20 20"><circle cx="10" cy="10" r="8.5" fill="none" stroke="#fff" stroke-width="1.6"/><ellipse cx="10" cy="10" rx="3.6" ry="8.5" fill="none" stroke="#fff" stroke-width="1.4"/><path d="M1.5 10h17M3 6h14M3 14h14" stroke="#fff" stroke-width="1.4"/></svg></div>
    <div class="contact-address">41 Willow Rd Parramatta</div>
  </div>

  <p class="brand-name" style="top:312px">Tessaly Clinics Australia</p>
  <div class="contact" style="top:307px;right:30px">
    <div class="contact-line">info@tessaly.co.uk
      <svg viewBox="0 0 20 20"><rect x="1" y="4" width="18" height="12" fill="none" stroke="#fff" stroke-width="1.6"/><path d="M1 4l9 7 9-7M1 16l7-6M19 16l-7-6" fill="none" stroke="#fff" stroke-width="1.6"/></svg></div>
    <div class="contact-line">www.tessaly.co.uk
      <svg viewBox="0 0 20 20"><circle cx="10" cy="10" r="8.5" fill="none" stroke="#fff" stroke-width="1.6"/><ellipse cx="10" cy="10" rx="3.6" ry="8.5" fill="none" stroke="#fff" stroke-width="1.4"/><path d="M1.5 10h17M3 6h14M3 14h14" stroke="#fff" stroke-width="1.4"/></svg></div>
    <div class="contact-address">41 Willow Rd Parramatta</div>
  </div>
</section>

<section class="card card-back">
  <span class="side-bar left" style="top:55px;background:var(--brown)"></span>
  <span class="side-bar right" style="top:55px;background:var(--brown)"></span>
  <span class="side-bar left" style="top:167px;background:var(--green)"></span>
  <span class="side-bar right" style="top:167px;background:var(--green)"></span>
  <span class="side-bar left" style="top:290px;background:var(--orange)"></span>
  <span class="side-bar right" style="top:290px;background:var(--orange)"></span>

  <p class="brand-name brand-corvane" style="top:74px">Corvane Clinics Australia</p>
  <p class="brand-name brand-lumora" style="top:188px">Lumora Clinics Australia</p>
  <p class="brand-name brand-tessaly" style="top:306px">Tessaly Clinics Australia</p>
</section>

</body>
</html>
```